Modern Business Card for Larkwell 2018

Our company assumes the best about people. We are creating an online community of entrepreneurs and business leaders who struggle with marketing their business online.

This business card should POP! We recently got a new logo and are launching a new website next month, so our business cards should make a statement that feels:
-Fresh
-Smart
-Trustworthy
-Fun

Target Market(s)

small business owners, entrepreneurs

Industry/Entity Type

Digital Marketing

Contact Information for Business Card

Dimensions: 3.5" x 2"

Font styles to use
Sans Serif

Colors
f37122
ffffff

Requirements
Must have
• We need a business card with a modern, bold design. We will use one side of the card as a lead-generation offer, so text on one side will need to fit up to 140 characters. The business card should stick to our core colors (orange, black, and white).
Nice to have
• We think a vertical "portrait" design could be interesting.
Should not have
• Should not look like a traditional business card. The round icon should stand out from a distance.

```html
<!DOCTYPE html>
<html lang="en">
<head>
<meta charset="utf-8">
<title>Larkwell Business Card</title>
<link rel="stylesheet" href="https://fonts.googleapis.com/css2?family=Montserrat:wght@800&family=Roboto:wght@400;700&family=Roboto+Condensed:wght@400;700&display=swap">
<style>
  :root {
    --brand-orange: #f36a28;
    --brand-orange-pale: #f6ddd0;
    --ink: #222222;
    --ink-soft: #555555;
    --card-white: #f1f1f1;
    --white: #ffffff;
    --backdrop: #1f1f1f;
    --rule: #333333;
  }
  * { margin: 0; padding: 0; box-sizing: border-box; }
  html, body { width: 1200px; height: 960px; overflow: hidden; }
  body { background: var(--backdrop); position: relative; font-family: "Roboto", sans-serif; }

  .card { position: absolute; width: 600px; height: 343px; overflow: hidden; }

  /* Front */
  .card-front { left: 314px; top: 113px; background: var(--card-white); }
  .front-decor { position: absolute; left: 0; top: 0; }
  .brand-dot { position: absolute; left: 131px; top: 39px; width: 40px; height: 40px; border-radius: 50%; background: var(--brand-orange); }
  .brand-name { position: absolute; left: 38px; top: 91px; font-family: "Montserrat", sans-serif; font-weight: 800; font-size: 36px; letter-spacing: 0.3px; color: var(--ink); line-height: 1; white-space: nowrap; }
  .brand-tagline { position: absolute; left: 40px; top: 133px; font-family: "Roboto", sans-serif; font-weight: 700; font-size: 11px; letter-spacing: 0.9px; color: var(--ink); white-space: nowrap; }
  .person { position: absolute; right: 40px; top: 166px; text-align: right; }
  .person-name { font-family: "Roboto Condensed", sans-serif; font-weight: 700; font-size: 24px; color: var(--brand-orange); line-height: 1.1; white-space: nowrap; }
  .person-title { font-family: "Roboto", sans-serif; font-size: 16px; color: var(--ink); margin-top: 2px; white-space: nowrap; }
  .accent-tab { position: absolute; right: 0; top: 162px; width: 13px; height: 56px; background: var(--brand-orange); }
  .contact-email { position: absolute; left: 39px; top: 288px; font-size: 15px; letter-spacing: 2.6px; color: var(--ink-soft); }

  /* Back */
  .card-back { left: 311px; top: 472px; background: var(--brand-orange); color: var(--white); }
  .offer-mark { position: absolute; left: 89px; top: 40px; width: 144px; height: 144px; border-radius: 50%; background: var(--white); }
  .offer-divider { position: absolute; left: 263px; top: 31px; width: 1px; height: 166px; background: rgba(255,255,255,0.7); }
  .offer-copy { position: absolute; left: 297px; top: 31px; }
  .offer-headline { font-family: "Roboto", sans-serif; font-weight: 700; font-size: 18.5px; line-height: 21px; text-transform: uppercase; white-space: nowrap; }
  .offer-body { font-size: 15px; line-height: 19.5px; margin-top: 4px; }
  .offer-url { font-family: "Roboto", sans-serif; font-weight: 700; font-size: 19px; margin-top: 7px; margin-left: -2px; white-space: nowrap; }
  .note-panel { position: absolute; left: 20px; top: 217px; width: 557px; height: 101px; background: var(--white); border-radius: 18px; }
  .note-line { position: absolute; left: 24px; right: 27px; height: 1px; background: var(--rule); }
  .note-line.first { top: 31px; }
  .note-line.second { top: 71px; }
</style>
</head>
<body>
  <section class="card card-front" aria-label="Front of business card">
    <svg class="front-decor" width="600" height="343" viewBox="0 0 600 343" aria-hidden="true">
      <circle cx="440" cy="168" r="165" fill="var(--brand-orange-pale)" opacity="0.75"/>
    </svg>
    <div class="brand-dot" aria-hidden="true"></div>
    <div class="brand-name">LARKWELL</div>
    <div class="brand-tagline">BUILD BRANDS THAT SPARK ACTION</div>
    <div class="person">
      <div class="person-name">DANA WHITFIELD</div>
      <div class="person-title">STORY MARKETING COACH</div>
    </div>
    <div class="accent-tab" aria-hidden="true"></div>
    <div class="contact-email">dana@larkwellnow.com</div>
  </section>

  <section class="card card-back" aria-label="Back of business card">
    <div class="offer-mark" aria-hidden="true"></div>
    <div class="offer-divider" aria-hidden="true"></div>
    <div class="offer-copy">
      <div class="offer-headline">Reach more people.<br>Make more money.<br>Create more impact.</div>
      <div class="offer-body">Get your free Larkwell<br>Starter Package and our<br>marketing guide today at</div>
      <div class="offer-url">Larkwellnow.com/start</div>
    </div>
    <div class="note-panel">
      <div class="note-line first"></div>
      <div class="note-line second"></div>
    </div>
  </section>
</body>
</html>
```